Kelvaro.ch is looking for business card letterhead and envelope C5 with WOW effect

We need a strong business card for our company Kelvaro.ch, logo is available. You want a black or dark background on which the logo Stark r% 26 # 252; appears. Letterhead and envelope in C5 format should be in a similar design, but does not have to be We need a strong business card for our company Kelvaro.ch, logo is available. A black or dark background is desired, on which the logo Stark comes across. The letterhead and the envelope in C5 format should have a similar design.

Target Market(s)

Private customers as well as entrepreneurs

Contact Information for Business Card

E-mail: info@kelvaro-example.ch
Web.www.Kelvaro-example.ch
Tel: +41 ( 0 ) 79 482 6037
Adresse:
Lindenweg 14
9406 Tarnbach

Hier kann man Icons verwenden für Email,Tel und Adressse

Font styles to use
Other font styles liked:
• Dubai,bold

Colors

Designer to choose colors to be used in the design.

Requirements
Must have
• WOW effect
Nice to have
• R% 26 # 252; back business card with our service listings. - VEHICLE LABELING - SHOP WINDOW LABELING - STICKERS AND MUCH MORE ... in red color

```html
<!DOCTYPE html>
<html lang="en">
<head>
<meta charset="utf-8">
<title>Kelvaro.ch Business Card</title>
<link rel="stylesheet" href="https://fonts.googleapis.com/css2?family=Montserrat:wght@700;800&family=Open+Sans:wght@400;600&display=swap">
<style>
  :root {
    --backdrop: #3e3935;
    --card-navy: #17233f;
    --card-navy-deep: #0f1a33;
    --accent-yellow: #f7c51c;
    --service-red: #d91e2a;
    --text-white: #ffffff;
    --text-soft: #e6e9f0;
  }
  * { margin: 0; padding: 0; box-sizing: border-box; }
  html, body { width: 1200px; height: 930px; overflow: hidden; }
  body {
    background: var(--backdrop);
    font-family: "Open Sans", sans-serif;
    color: var(--text-white);
    position: relative;
  }
  .card {
    position: absolute;
    width: 580px;
    height: 330px;
    border-radius: 18px;
    background: linear-gradient(135deg, var(--card-navy) 0%, var(--card-navy-deep) 100%);
    box-shadow: 0 14px 30px rgba(0,0,0,0.45);
    overflow: hidden;
  }
  .card-front { left: 150px; top: 90px; }
  .card-back { left: 470px; top: 500px; }

  .wordmark {
    position: absolute;
    font-family: "Montserrat", sans-serif;
    font-weight: 800;
    font-size: 40px;
    letter-spacing: 1px;
    text-transform: uppercase;
    color: var(--text-white);
    white-space: nowrap;
  }
  .card-front .wordmark { left: 210px; top: 96px; }
  .card-back .wordmark { right: 42px; top: 34px; font-size: 38px; }

  .service-list {
    position: absolute;
    left: 210px;
    top: 170px;
    list-style: none;
    font-size: 14px;
    letter-spacing: 0.2px;
    text-transform: uppercase;
    color: var(--text-soft);
    line-height: 26px;
  }
  .service-list li::before {
    content: "";
    display: inline-block;
    width: 7px; height: 7px;
    border-radius: 50%;
    background: var(--service-red);
    margin-right: 10px;
    vertical-align: middle;
  }

  .person {
    position: absolute;
    right: 42px;
    top: 122px;
    text-align: right;
  }
  .person-name {
    font-family: "Montserrat", sans-serif;
    font-weight: 800;
    font-size: 26px;
    letter-spacing: 1.5px;
    text-transform: uppercase;
  }
  .person-name .surname { color: var(--accent-yellow); }
  .person-role { font-size: 14px; margin-top: 2px; color: var(--text-soft); }
  .name-rule {
    position: absolute;
    right: 42px; top: 162px;
    width: 300px; height: 1px;
    background: var(--accent-yellow);
  }
  .address {
    position: absolute;
    right: 42px; top: 206px;
    font-size: 14px;
    color: var(--text-soft);
  }

  .contact-rule {
    position: absolute;
    left: 36px; top: 218px;
    width: 250px; height: 1px;
    background: var(--accent-yellow);
  }
  .contact-list {
    position: absolute;
    left: 36px; top: 230px;
    list-style: none;
    font-size: 15px;
    line-height: 26px;
    color: var(--text-soft);
  }
  .contact-list li { display: flex; align-items: center; gap: 10px; }
  .contact-list svg { width: 14px; height: 14px; flex: none; }
</style>
</head>
<body>

  <section class="card card-front" aria-label="Business card front">
    <div class="wordmark">Kelvaro.ch</div>
    <ul class="service-list">
      <li>Stickers and much more</li>
      <li>Shop window labeling</li>
      <li>Vehicle labeling</li>
    </ul>
  </section>

  <section class="card card-back" aria-label="Business card back">
    <div class="wordmark">Kelvaro.ch</div>
    <div class="person">
      <div class="person-name">Marco <span class="surname">Hediger</span></div>
      <div class="person-role">Director</div>
    </div>
    <div class="name-rule"></div>
    <div class="address">Lindenweg 14 9406 Tarnbach</div>

    <div class="contact-rule"></div>
    <ul class="contact-list">
      <li>
        <svg viewBox="0 0 24 24" aria-hidden="true"><path fill="#f7c51c" d="M6.6 10.8a15.1 15.1 0 0 0 6.6 6.6l2.2-2.2a1 1 0 0 1 1-.25 11.4 11.4 0 0 0 3.6.57 1 1 0 0 1 1 1V20a1 1 0 0 1-1 1A17 17 0 0 1 3 4a1 1 0 0 1 1-1h3.5a1 1 0 0 1 1 1c0 1.25.2 2.45.57 3.6a1 1 0 0 1-.25 1z"/></svg>
        +41 ( 0 ) 79 482 6037
      </li>
      <li>
        <svg viewBox="0 0 24 24" aria-hidden="true"><rect x="3" y="5" width="18" height="14" rx="1.5" fill="none" stroke="#f7c51c" stroke-width="2"/><path d="M3.5 6l8.5 7 8.5-7" fill="none" stroke="#f7c51c" stroke-width="2"/></svg>
        info@kelvaro-example.ch
      </li>
      <li>
        <svg viewBox="0 0 24 24" aria-hidden="true"><circle cx="12" cy="12" r="9" fill="none" stroke="#f7c51c" stroke-width="2"/><ellipse cx="12" cy="12" rx="4" ry="9" fill="none" stroke="#f7c51c" stroke-width="1.6"/><path d="M3 12h18M5 7.5h14M5 16.5h14" stroke="#f7c51c" stroke-width="1.6"/></svg>
        www.kelvaro-example.ch
      </li>
    </ul>
  </section>

</body>
</html>
```